Business Card Design

We are a law firm which provides services to creditors.....we do collection litigation. I am wide open on suggestions. I was thinking of a square card? Alternatively, a vertically oriented standard card or a folded card.....something unique. I would like to use my firm logo and beyond that, I am open for any and all suggestions. I'm uncertain if the complete log is uploaded? If not, please let me email it to you.

Industry/Entity Type

Law Firm

Contact Information for Business Card

Hart, Crane & Dobbs, P.C.
Tom Dobbs, Lawyer
4387 N Larkspur Ave
Oklahoma City, OK 73924
tdobbs@HcdCounsel.com
www.HcdCounsel.com
mobile: 405-382-7914

```html
<!DOCTYPE html>
<html lang="en">
<head>
<meta charset="utf-8">
<title>Hart, Crane &amp; Dobbs, P.C. — Business Card</title>
<link rel="stylesheet" href="https://fonts.googleapis.com/css2?family=Montserrat:wght@400;700&display=swap">
<style>
  :root {
    --backdrop: #e9e4da;
    --green: #17974a;
    --green-deep: #0f7a39;
    --gold: #c9c21a;
    --gold-light: #ddd63a;
    --cream: #f3ecd2;
    --rule: rgba(243, 236, 210, 0.55);
    --ink-light: #f6f1dc;
  }
  * { margin: 0; padding: 0; box-sizing: border-box; }
  html, body {
    width: 1200px; height: 902px; overflow: hidden;
    background: var(--backdrop);
    font-family: "Montserrat", Arial, sans-serif;
  }
  .canvas { position: relative; width: 1200px; height: 902px; }
  .card {
    position: absolute; width: 540px; height: 310px;
    border-radius: 4px; overflow: hidden;
    box-shadow: 0 10px 24px rgba(60, 45, 20, 0.25);
    color: var(--ink-light);
  }
  .card--front { left: 70px; top: 80px; }
  .card--back { left: 590px; top: 512px; }
  .card__surface { position: absolute; inset: 0; width: 100%; height: 100%; }
  .firm-name {
    position: absolute; left: 40px; top: 78px;
    font-weight: 700; font-size: 32px; letter-spacing: 0.2px;
    white-space: nowrap;
  }
  .firm-rule {
    position: absolute; left: 40px; right: 40px; top: 126px;
    height: 1px; background: var(--rule);
  }
  .firm-mark {
    position: absolute; display: flex; align-items: center; gap: 10px;
    font-weight: 700; font-size: 15px; color: var(--cream);
  }
  .firm-mark__dot {
    width: 28px; height: 28px; border-radius: 50%;
    background: var(--gold);
  }
  .card--front .firm-mark { left: 170px; top: 170px; }
  .card--back .firm-name { left: 30px; top: 66px; font-size: 28px; }
  .card--back .firm-rule { left: 30px; right: 30px; top: 108px; }
  .card--back .firm-mark { left: 50px; top: 200px; font-size: 13px; }
  .holder {
    position: absolute; right: 34px; top: 118px; text-align: right;
  }
  .holder__name { font-size: 24px; font-weight: 400; line-height: 1; }
  .holder__title { font-size: 10px; margin-top: 2px; }
  .holder-rule {
    position: absolute; right: 30px; width: 210px; top: 166px;
    height: 1px; background: var(--rule);
  }
  .contact-list {
    position: absolute; right: 30px; top: 176px; width: 210px;
    list-style: none; font-size: 10.5px; line-height: 1.25;
  }
  .contact-list li { display: flex; align-items: flex-start; gap: 8px; margin-bottom: 6px; }
  .contact-list svg { flex: none; width: 14px; height: 14px; }
  .contact-rule {
    position: absolute; right: 30px; width: 210px; top: 272px;
    height: 1px; background: var(--rule);
  }
</style>
</head>
<body>
<main class="canvas">

  <section class="card card--front" aria-label="Card front">
    <svg class="card__surface" viewBox="0 0 540 310" preserveAspectRatio="none" aria-hidden="true">
      <rect width="540" height="310" fill="var(--green)"/>
      <polygon points="0,0 290,0 260,46 0,46" fill="var(--gold)"/>
      <polygon points="290,0 302,0 272,46 260,46" fill="var(--cream)"/>
      <rect x="108" y="0" width="7" height="46" fill="var(--cream)"/>
      <polygon points="540,310 240,310 272,258 540,258" fill="var(--gold)"/>
      <polygon points="240,310 228,310 260,258 272,258" fill="var(--cream)"/>
      <rect x="420" y="258" width="7" height="52" fill="var(--cream)"/>
      <rect x="0" y="46" width="540" height="212" fill="url(#frontShade)"/>
      <defs>
        <linearGradient id="frontShade" x1="0" y1="0" x2="1" y2="0">
          <stop offset="0" stop-color="#ffffff" stop-opacity="0.06"/>
          <stop offset="1" stop-color="#000000" stop-opacity="0.12"/>
        </linearGradient>
      </defs>
    </svg>
    <h1 class="firm-name">Hart, Crane &amp; Dobbs, P.C.</h1>
    <div class="firm-rule"></div>
    <div class="firm-mark"><span class="firm-mark__dot"></span>Hart, Crane &amp; Dobbs</div>
  </section>

  <section class="card card--back" aria-label="Card back">
    <svg class="card__surface" viewBox="0 0 540 310" preserveAspectRatio="none" aria-hidden="true">
      <rect width="540" height="310" fill="var(--green)"/>
      <polygon points="0,0 300,0 272,44 0,44" fill="var(--gold)"/>
      <polygon points="300,0 312,0 284,44 272,44" fill="var(--cream)"/>
      <rect x="102" y="0" width="7" height="44" fill="var(--cream)"/>
      <polygon points="540,310 250,310 282,262 540,262" fill="var(--gold)"/>
      <polygon points="250,310 238,310 270,262 282,262" fill="var(--cream)"/>
      <rect x="430" y="262" width="7" height="48" fill="var(--cream)"/>
    </svg>
    <h2 class="firm-name">Hart, Crane &amp; Dobbs, P.C.</h2>
    <div class="firm-rule"></div>
    <div class="firm-mark"><span class="firm-mark__dot"></span>Hart, Crane &amp; Dobbs</div>

    <div class="holder">
      <p class="holder__name">Tom Dobbs</p>
      <p class="holder__title">Lawyer</p>
    </div>
    <div class="holder-rule"></div>
    <ul class="contact-list">
      <li>
        <svg viewBox="0 0 14 14"><circle cx="7" cy="7" r="6.3" fill="none" stroke="currentColor" stroke-width="1"/><rect x="5" y="3.5" width="4" height="7" rx="0.8" fill="none" stroke="currentColor" stroke-width="0.9"/></svg>
        <span>405-382-7914</span>
      </li>
      <li>
        <svg viewBox="0 0 14 14"><circle cx="7" cy="7" r="6.3" fill="none" stroke="currentColor" stroke-width="1"/><rect x="3.8" y="4.2" width="6.4" height="4.4" fill="none" stroke="currentColor" stroke-width="0.9"/><line x1="5.5" y1="10.2" x2="8.5" y2="10.2" stroke="currentColor" stroke-width="0.9"/></svg>
        <span>www.HcdCounsel.com</span>
      </li>
      <li>
        <svg viewBox="0 0 14 14"><circle cx="7" cy="7" r="6.3" fill="none" stroke="currentColor" stroke-width="1"/><rect x="3.8" y="4.8" width="6.4" height="4.4" fill="none" stroke="currentColor" stroke-width="0.9"/><polyline points="3.8,4.8 7,7.4 10.2,4.8" fill="none" stroke="currentColor" stroke-width="0.9"/></svg>
        <span>tdobbs@HcdCounsel.com</span>
      </li>
      <li>
        <svg viewBox="0 0 14 14"><circle cx="7" cy="7" r="6.3" fill="none" stroke="currentColor" stroke-width="1"/><path d="M7 10.8 C5 8.4 4.4 7.4 4.4 6.1 a2.6 2.6 0 0 1 5.2 0 C9.6 7.4 9 8.4 7 10.8Z" fill="currentColor"/></svg>
        <span>4387 N Larkspur Ave<br>Oklahoma City, OK 73924</span>
      </li>
    </ul>
    <div class="contact-rule"></div>
  </section>

</main>
</body>
</html>
```